Brand New Product Needs Sales Focused Website Design

Looking for design of Homepage, Category Page & Product Page for single product sales focused website. TrundleCrate manufacture and distribute a brand new product to the market called PalTote-Case which is a super strong, re-useable, folding & stacking plastic box which can be seen on our current website www.paltote-case.example PalTote-Case was originally developed as an alternative to supermarket carrier bags and was pitched as a box for life against the other low end re-useable products. The original version was made from recycled plastic and pitched very much as environmental product. We are now taking a different direction and have re-designed the boxes in 5 bright and fashionable designs and although we still want the primary focus to be supermarket shopping we want to position the product as a design led, must have shopping and household accessory rather than a boring, cheap looking black plastic box. The new designs will still have the environmental benefits of being able to be re-used thousands of times and being 100% recyclable and save on the imminent 5p tax on carrier bags in the UK however the new designs will not be made from recycled material. Although the main use for PalTote-Case is supermarket shopping it has a multitude of other uses especially where you need temporary storage - laundry, back of the car, moving house/students, gardening, days out, home office filing (will take A4 file), recycling and much more - PalTote-Case is made out of super strong Polypropylene and can be easily washed and sanitised after use and can be folded and unfolded thousands of times and so will last for many years. PalTote-Case is a product that needs to be seen in action to be understood so the web design must quickly and easily communicate what PalTote-Case is and how it works - this can be done with video, images and copy. Our current website does not work for many reasons:- it is too busy, has too much information, tries too hard and ultimately isn't working. Any of the images off our current website can be supplied for use. Once the concept of the website is agreed I can get these photoshopped with the new designs. Pictures of new designs for reference will be attached to this brief. Ultimately we want the website to convert visitors to sales and therefore designers with a proven track record in this field are especially welcome to enter. We also have a Dropbox folder with over 100 product and situation images in - please send email address and we will send an invite to the folder. Due to Christmas period this competition will be run over 15 days however we may choose to extend the deadline to account for the non working days. Any questions feel free to ask - we will respond within 24 hours where possible.

```html
<!DOCTYPE html>
<html lang="en">
<head>
<meta charset="utf-8">
<title>PalTote-Case – Home</title>
<link href="https://fonts.googleapis.com/css2?family=Lobster&family=PT+Sans:wght@400;700&display=swap" rel="stylesheet">
<style>
:root{
  --green:#8cc063;
  --green-soft:#93c46b;
  --green-dark:#4c8a2a;
  --green-deep:#3f7a22;
  --green-brand:#6db33f;
  --ink:#2b2b2b;
  --grey:#8a8a8a;
  --line:#d4d4d4;
  --white:#ffffff;
  --head-bg:#f4f4f4;
}
*{margin:0;padding:0;box-sizing:border-box}
html,body{width:677px;height:1200px;overflow:hidden;background:var(--white)}
body{font-family:'PT Sans',sans-serif;color:var(--ink);position:relative}
.abs{position:absolute}
.script{font-family:'Lobster',cursive;font-weight:400}
.btn{position:absolute;background:var(--green-dark);color:var(--white);font-size:10px;display:flex;align-items:center;justify-content:center;border-radius:2px;box-shadow:0 1px 0 #2f5f18}

/* header */
.site-header{top:0;left:0;width:677px;height:56px;background:var(--head-bg);border-top:3px solid var(--green-brand);border-bottom:1px solid #e2e2e2}
.brand{left:118px;top:8px;font-weight:700;font-size:19px;color:var(--green-brand);display:flex;align-items:center;gap:5px}
.brand-mark{width:12px;height:12px;background:var(--green-brand);border-radius:2px}
.top-info{top:9px;left:392px;font-size:7.5px;display:flex;gap:20px;align-items:center}
.top-info span{display:flex;align-items:center;gap:4px}
.main-nav{top:35px;left:247px;display:flex;gap:13px;font-size:9px}
.main-nav a{color:var(--ink);text-decoration:none;padding-bottom:2px}
.main-nav a.active{border-bottom:2px solid var(--green-brand)}
.search{top:35px;left:478px;width:82px;height:13px;border:1px solid var(--green-brand);background:var(--white)}
.search-btn{top:35px;left:543px;width:17px;height:13px;background:var(--green-brand)}

/* hero */
.hero{top:56px;left:0;width:677px;height:227px;background:var(--white)}
.hero h1{position:absolute;left:118px;top:36px;font-size:15px;color:#3a3a3a}
.hero p{position:absolute;left:118px;top:60px;width:266px;font-size:8.8px;line-height:11.3px;color:var(--grey)}
.hero-photo{left:378px;top:0;width:176px;height:227px;background:linear-gradient(160deg,#e8d7cc,#2b2b2b 60%,#35a86c)}
.dots{left:322px;top:211px;display:flex;gap:8px}
.dots i{width:5px;height:5px;border-radius:50%;background:#222;display:block}

/* how it works */
.how{top:283px;left:0;width:677px;height:156px;background:var(--green)}
.how h2{position:absolute;left:126px;top:15px;font-size:13px;color:var(--white)}
.how p{position:absolute;left:126px;top:33px;width:206px;font-size:7.4px;line-height:11.5px;color:var(--white)}
.demo-btn{left:126px;top:107px;width:118px;height:21px;font-size:11px}
.video{left:344px;top:20px;width:206px;height:109px;border:2px solid #6e9e48;background:linear-gradient(120deg,#2b4fb0,#5a6b4e 55%,#c7a489)}
.video-bar{left:0;bottom:0;width:100%;height:14px;background:rgba(0,0,0,.8);color:#ddd;font-size:6px;display:flex;align-items:center;justify-content:space-between;padding:0 6px}
.play{left:95px;top:44px;width:20px;height:13px;background:rgba(255,255,255,.35);border-radius:3px}

/* why */
.why{top:439px;left:0;width:677px;height:218px}
.why-photo{left:128px;top:11px;width:153px;height:207px;background:linear-gradient(170deg,#d9b79e,#39b36b 45%,#1f1f1f 75%)}
.why h2{position:absolute;left:298px;top:18px;font-size:13px;color:#2b2b2b}
.feature{position:absolute;width:135px;height:40px}
.feature .icon{position:absolute;left:0;top:0;width:31px;height:31px}
.feature h3{position:absolute;left:37px;top:0;font-size:8.5px;font-weight:700}
.feature p{position:absolute;left:37px;top:12px;font-size:6.5px;line-height:9px;color:var(--grey);width:82px}

/* products */
.products{top:657px;left:0;width:677px;height:169px;background:var(--green)}
.products h2{position:absolute;left:0;width:677px;text-align:center;top:13px;font-size:12.5px;color:#2b2b2b}
.card{position:absolute;top:45px;width:71px;height:75px;border:1px solid #5e9638;background:var(--green-soft)}
.card .thumb{position:absolute;left:5px;top:5px;width:59px;height:43px;border-radius:3px}
.card .name{position:absolute;left:0;width:100%;top:51px;text-align:center;font-size:6.5px}
.card .price{position:absolute;left:0;width:100%;top:62px;text-align:center;font-size:6.5px}
.card .price s{margin-right:8px}
.cart{position:absolute;top:126px;width:56px;height:11px;font-size:6px;font-weight:700}

/* testimonial */
.testimonial{top:826px;left:0;width:677px;height:218px}
.testimonial h2{position:absolute;left:0;width:677px;text-align:center;top:17px;font-size:12.5px}
.avatar{left:136px;top:48px;width:76px;height:76px;border-radius:50%;border:2px solid var(--green-dark);background:linear-gradient(#e9e3de,#3a3a3a)}
.person{left:120px;top:128px;width:110px;text-align:center;font-size:8.5px;font-weight:700}
.quote{left:241px;top:47px;width:306px;height:104px;border:1px solid var(--line);border-radius:3px;padding:10px 12px 0 12px;font-size:6.8px;line-height:11.2px;color:var(--grey)}
.quote::before{content:"";position:absolute;left:-6px;top:54px;width:9px;height:9px;background:var(--white);border-left:1px solid var(--line);border-bottom:1px solid var(--line);transform:rotate(45deg)}
.more-btn{left:307px;top:171px;width:63px;height:18px}

/* footer */
.site-footer{top:1044px;left:0;width:677px;height:129px;background:var(--green)}
.site-footer h4{position:absolute;font-size:9.5px;color:#2f4f1c;font-weight:700;letter-spacing:.3px}
.quick{position:absolute;left:144px;top:42px;font-size:7.5px;line-height:15px;color:var(--white);list-style:none}
.vline{position:absolute;top:25px;width:1px;height:90px;background:rgba(255,255,255,.6)}
.contact{position:absolute;left:243px;top:50px;font-size:6.8px;color:var(--white);line-height:13px}
.contact div{display:flex;gap:8px;margin-bottom:5px}
.social{position:absolute;left:441px;top:40px;display:flex;gap:7px}
.social span{width:18px;height:18px;border-radius:2px;font-size:5px;color:var(--white);display:flex;align-items:center;justify-content:center}
.awards{position:absolute;left:442px;top:80px;font-size:5px;line-height:9.5px;color:var(--white)}
.bottom-bar{top:1173px;left:0;width:677px;height:27px;background:var(--green-deep);color:var(--white);font-size:7px}
.bottom-bar .copy{position:absolute;left:126px;top:9px}
.cards-row{position:absolute;left:462px;top:6px;display:flex;gap:3px}
.cards-row span{width:21px;height:14px;background:var(--white);border-radius:2px;font-size:4.5px;color:#333;display:flex;align-items:center;justify-content:center}
</style>
</head>
<body>

<header class="site-header abs">
  <div class="brand abs"><span class="brand-mark"></span>PalTote-Case</div>
  <div class="top-info abs">
    <span><svg width="7" height="8" viewBox="0 0 7 8"><path d="M1 0.5 L2.5 0.5 L3 2.5 L2 3.2 Q3 5 4.3 5.8 L5 4.8 L7 5.3 L7 7 Q3.5 7.8 1.5 4.5 Q0.5 2.5 1 0.5Z" fill="#6db33f"/></svg>+44-100-555-0142</span>
    <span><svg width="8" height="9" viewBox="0 0 8 9"><rect x="0" y="2.5" width="8" height="6.5" rx="1" fill="#6db33f"/><path d="M2.3 3V1.6a1.7 1.7 0 0 1 3.4 0V3" stroke="#6db33f" fill="none"/></svg>My shopping bag (0)</span>
  </div>
  <nav class="main-nav abs">
    <a class="active" href="#">Home</a><a href="#">Category</a><a href="#">Products</a><a href="#">Gurantee</a><a href="#">Contact Us</a>
  </nav>
  <div class="search abs"></div>
  <div class="search-btn abs"><svg width="17" height="13" viewBox="0 0 17 13"><circle cx="8" cy="6" r="2.6" stroke="#fff" stroke-width="1.2" fill="none"/><line x1="9.9" y1="7.9" x2="11.5" y2="9.5" stroke="#fff" stroke-width="1.3"/></svg></div>
</header>

<section class="hero abs">
  <h1 class="script">Welcome To PalTote-Case</h1>
  <p>Lorem Ipsum is simply dummy text of the printing and typesetting industry. Lorem Ipsum has been the industry's standard dummy text ever since the 1500s, when an unknown printer took a galley of type and scrambled it to make a type specimen book. It has survived not only five centuries</p>
  <div class="btn" style="left:118px;top:185px;width:62px;height:19px">Read More</div>
  <div class="hero-photo abs" role="img" aria-label="Smiling woman holding up a black folding PalTote-Case box"></div>
  <div class="dots abs"><i></i><i></i><i></i><i></i></div>
</section>

<section class="how abs">
  <h2 class="script">How It Works</h2>
  <p>Lorem Ipsum is simply dummy text of the printing and typesetting industry. Lorem Ipsum has been the industry's standard dummy text ever since the 1500s, when an unknown printer took a galley of type and scrambled it to make a type specimen book. It has survived not only five centuries</p>
  <div class="btn demo-btn">View Our Live Demo</div>
  <div class="video abs" role="img" aria-label="Demo video still of a woman unfolding a blue box in a kitchen">
    <div class="play abs"><svg width="20" height="13" viewBox="0 0 20 13"><path d="M8 3.5 L13 6.5 L8 9.5Z" fill="#fff"/></svg></div>
    <div class="video-bar abs"><span>❚❚</span><span>04:29 | 02:47</span></div>
  </div>
</section>

<section class="why abs">
  <div class="why-photo abs" role="img" aria-label="Woman carrying an open box full of groceries"></div>
  <h2 class="script">Why PalTote-Case</h2>

  <div class="feature" style="left:298px;top:50px">
    <svg class="icon" viewBox="0 0 31 31"><circle cx="15.5" cy="15.5" r="14.5" fill="#fff" stroke="#6db33f" stroke-width="1.5"/><circle cx="15.5" cy="15.5" r="11" fill="#6db33f"/><path d="M10 14a6 6 0 0 1 10.5-3M21 17a6 6 0 0 1-10.5 3" stroke="#fff" stroke-width="1.8" fill="none"/><path d="M20.5 8v3.5h-3.5M10.5 23v-3.5h3.5" stroke="#fff" stroke-width="1.5" fill="none"/></svg>
    <h3>Reusable</h3><p>Lorem Ipsum is simply dummy text of the print-</p>
  </div>
  <div class="feature" style="left:440px;top:50px">
    <svg class="icon" viewBox="0 0 31 31"><circle cx="15.5" cy="15.5" r="14.5" fill="#fff" stroke="#6db33f" stroke-width="1.5"/><circle cx="15.5" cy="15.5" r="11" fill="#6db33f"/><path d="M9 14h13l-2 7h-9z" fill="none" stroke="#fff" stroke-width="1.5"/><path d="M12 11l2 3M18 10l-2 4" stroke="#fff" stroke-width="1.3"/></svg>
    <h3>Easy Washable</h3><p>Lorem Ipsum is simply dummy text of the print-</p>
  </div>
  <div class="feature" style="left:298px;top:111px">
    <svg class="icon" viewBox="0 0 31 31"><circle cx="15.5" cy="15.5" r="14.5" fill="#fff" stroke="#6db33f" stroke-width="1.5"/><circle cx="15.5" cy="15.5" r="11" fill="#6db33f"/><circle cx="15.5" cy="12.5" r="4.5" fill="none" stroke="#fff" stroke-width="1.4"/><path d="M15.5 17v6M12.5 23h6" stroke="#fff" stroke-width="1.4"/></svg>
    <h3>Eco Friendly Product</h3><p>Lorem Ipsum is simply dummy text of the print-</p>
  </div>
  <div class="feature" style="left:440px;top:111px">
    <svg class="icon" viewBox="0 0 31 31"><circle cx="15.5" cy="15.5" r="14.5" fill="#fff" stroke="#6db33f" stroke-width="1.5"/><circle cx="15.5" cy="15.5" r="11" fill="#6db33f"/><rect x="9" y="14" width="8" height="4.5" rx="2.2" transform="rotate(-45 13 16)" fill="none" stroke="#fff" stroke-width="1.5"/><rect x="14" y="12" width="8" height="4.5" rx="2.2" transform="rotate(-45 18 14)" fill="none" stroke="#fff" stroke-width="1.5"/></svg>
    <h3>Super Strong</h3><p>Lorem Ipsum is simply dummy text of the print-</p>
  </div>
  <div class="feature" style="left:298px;top:168px">
    <svg class="icon" viewBox="0 0 31 31"><circle cx="15.5" cy="15.5" r="14.5" fill="#fff" stroke="#6db33f" stroke-width="1.5"/><circle cx="15.5" cy="15.5" r="11" fill="#6db33f"/><path d="M15.5 9l3.5 6h-7zM10 21l3.5-6 3.5 6zM17 21l3.5-6 1 6z" fill="none" stroke="#fff" stroke-width="1.3"/></svg>
    <h3>Recycle</h3><p>Lorem Ipsum is simply dummy text of the print-</p>
  </div>
  <div class="feature" style="left:440px;top:168px">
    <svg class="icon" viewBox="0 0 31 31"><circle cx="15.5" cy="15.5" r="14.5" fill="#fff" stroke="#6db33f" stroke-width="1.5"/><circle cx="15.5" cy="15.5" r="11" fill="#6db33f"/><path d="M10 21V10l4 4 3-4 4 4v7l-4-4-3 4-4-4" fill="none" stroke="#fff" stroke-width="1.4"/></svg>
    <h3>Foldable</h3><p>Lorem Ipsum is simply dummy text of the print-</p>
  </div>
</section>

<section class="products abs">
  <h2 class="script">Our Products</h2>
  <div class="card" style="left:158px"><div class="thumb" role="img" aria-label="Tan leather-look box" style="background:linear-gradient(#c56a3a,#8a3f1e)"></div><div class="name">PalTote box1</div><div class="price"><s>$40.24</s>$25.24</div></div>
  <div class="card" style="left:241px"><div class="thumb" role="img" aria-label="Blue leather-look box" style="background:linear-gradient(#6aa2d8,#2d5f98)"></div><div class="name">PalTote box2</div><div class="price"><s>$40.24</s>$25.24</div></div>
  <div class="card" style="left:323px"><div class="thumb" role="img" aria-label="Woven wicker-look box" style="background:linear-gradient(#d8c3a0,#8f7455)"></div><div class="name">PalTote box3</div><div class="price"><s>$40.24</s>$25.24</div></div>
  <div class="card" style="left:406px"><div class="thumb" role="img" aria-label="Leopard print box with red lid" style="background:linear-gradient(#a8283a 30%,#d6a660)"></div><div class="name">PalTote box4</div><div class="price"><s>$40.24</s>$25.24</div></div>
  <div class="card" style="left:489px"><div class="thumb" role="img" aria-label="Floral pastel pattern box" style="background:linear-gradient(#d8e4ea,#e7b6c4)"></div><div class="name">PalTote box5</div><div class="price"><s>$40.24</s>$25.24</div></div>
  <div class="btn cart" style="left:165px">ADD TO CART</div>
  <div class="btn cart" style="left:248px">ADD TO CART</div>
  <div class="btn cart" style="left:330px">ADD TO CART</div>
  <div class="btn cart" style="left:413px">ADD TO CART</div>
  <div class="btn cart" style="left:496px">ADD TO CART</div>
</section>

<section class="testimonial abs">
  <h2 class="script">What Our Customer Says</h2>
  <div class="avatar abs" role="img" aria-label="Customer portrait"></div>
  <div class="person abs">JUNE ORRELL</div>
  <div class="quote abs">Lorem Ipsum is simply dummy text of the printing and typesetting industry. Lorem Ipsum has been the industry's standard dummy text ever since the 1500s, when an unknown printer took a galley of type and scrambled it to make a type specimen book. It has survived not only five centuries, but also the leap into electronic typesetting, remaining essentially unchanged. It was popularised in the 1960s with the release of Typeframe sheets containing Lorem Ipsum passages, and more recently with desktop publishing software like Pagecraft Studio including versions of Lorem Ipsum.</div>
  <div class="btn more-btn">View More</div>
</section>

<footer class="site-footer abs">
  <h4 style="left:142px;top:22px">Quick Links</h4>
  <ul class="quick"><li>Home</li><li>Products</li><li>Categories</li><li>Gurantee</li><li>Contact Us</li></ul>
  <div class="vline" style="left:220px"></div>
  <h4 style="left:243px;top:21px">Contact Us</h4>
  <div class="contact">
    <div><svg width="6" height="9" viewBox="0 0 6 9"><path d="M3 9 L0.4 4A3 3 0 1 1 5.6 4Z" fill="#fff"/><circle cx="3" cy="3" r="1" fill="#8cc063"/></svg><span>Lorem Ipsum is simply dummy text of the<br>printing and typesetting industry. Lorem</span></div>
    <div><svg width="7" height="8" viewBox="0 0 7 8"><path d="M1 0.5 L2.5 0.5 L3 2.5 L2 3.2 Q3 5 4.3 5.8 L5 4.8 L7 5.3 L7 7 Q3.5 7.8 1.5 4.5 Q0.5 2.5 1 0.5Z" fill="#fff"/></svg><span>+44-100-555-0142</span></div>
    <div><svg width="8" height="7" viewBox="0 0 8 7"><rect x="0.5" y="1" width="7" height="5.5" fill="none" stroke="#fff"/><path d="M0.5 1 L4 4 L7.5 1" stroke="#fff" fill="none"/></svg><span>www.paltote-case.example</span></div>
  </div>
  <div class="vline" style="left:417px"></div>
  <h4 style="left:441px;top:21px">Fallow Us On</h4>
  <div class="social"><span style="background:#2ea3e3">Chirp</span><span style="background:#d8322b">Vidz</span><span style="background:#3b5998">Circl</span><span style="background:#1a7ab5">Linq</span></div>
  <h4 style="left:442px;top:66px">Awards</h4>
  <div class="awards">Future Homes Weekly<br>Northern Housewares Guild<br>Fenland Evening Post<br>Grand Home Living Show</div>
</footer>

<div class="bottom-bar abs">
  <span class="copy">All Rights Reserved@ 2014 www.paltote-case.example</span>
  <div class="cards-row"><span>Paywell</span><span>Cardex</span><span>Amberpay</span><span>Novacard</span></div>
</div>

</body>
</html>
```